Brightway Haul & Upkeep Services, are a company that offers a 'one stop shop' pre-move clean up a

I have already selected a logo which I would like on the front of the business cards along with phone numbers, web address and email which are:
0487650392
www.brightwayhaul.com.au
brightwayhaulandupkeep@mailbox.example

On the back of the card I would like to list some of the types of service we offer (clean - move - repairs/maintenance) which are:
CLEAN - windows, gutters, solar panels, driveways/paths, carpets.
MOVE - Small/medium size house/office moves, large item pick-up & delivery, yard clean-up and removal.
General maintenance and repairs.

I would like the blue logo on a gray background.

Thanks

```html
<!DOCTYPE html>
<html lang="en">
<head>
<meta charset="utf-8">
<title>Brightway Haul &amp; Upkeep Services – Business Cards</title>
<link rel="stylesheet" href="https://fonts.googleapis.com/css2?family=Open+Sans:wght@400;600;700;800&display=swap">
<style>
  :root {
    --stage: #c98a55;
    --card-grey: #cfd0d2;
    --card-grey-light: #dcdddf;
    --card-black: #050505;
    --brand-blue: #1e6fba;
    --brand-blue-light: #7cb9e8;
    --ink: #1b1b1b;
    --white: #ffffff;
    --label: #ffffff;
  }
  * { box-sizing: border-box; margin: 0; padding: 0; }
  html, body {
    width: 1200px; height: 762px; overflow: hidden;
    background: var(--stage);
    font-family: "Open Sans", Arial, sans-serif;
  }
  .sheet { position: relative; width: 1200px; height: 762px; }

  .side-label {
    position: absolute; top: 14px; width: 540px; text-align: center;
    color: var(--label); font-size: 38px; font-weight: 400;
  }
  .side-label--one { left: 9px; }
  .side-label--two { left: 604px; }

  .card {
    position: absolute; width: 540px; height: 308px; overflow: hidden;
    border: 1px solid rgba(0,0,0,0.35);
  }
  .card--front-grey { left: 43px; top: 77px; background: var(--card-grey); }
  .card--front-black { left: 620px; top: 77px; background: var(--card-black); }
  .card--back { left: 326px; top: 419px; width: 539px; height: 307px; background: var(--card-grey-light); }

  .card__wave { position: absolute; inset: 0; width: 100%; height: 100%; }

  .brand-name {
    position: absolute; color: var(--brand-blue); font-weight: 800;
    text-transform: uppercase; line-height: 1.02; letter-spacing: 0.5px;
  }
  .brand-name__main { display: block; font-size: 40px; }
  .brand-name__sub { display: block; font-size: 20px; margin-top: 6px; }
  .card--front-grey .brand-name,
  .card--front-black .brand-name { left: 40px; top: 78px; }
  .card--back .brand-name { left: 30px; top: 52px; }
  .card--back .brand-name__main { font-size: 29px; }
  .card--back .brand-name__sub { font-size: 15px; margin-top: 4px; }

  .contact-phone {
    position: absolute; left: 48px; top: 214px;
    font-size: 20px; display: flex; align-items: center; gap: 8px;
  }
  .card--front-grey .contact-phone { color: var(--ink); }
  .card--front-black .contact-phone { color: var(--white); }
  .contact-phone svg { width: 16px; height: 16px; }

  .contact-web {
    position: absolute; right: 12px; top: 262px;
    color: var(--white); font-size: 15px; letter-spacing: 0.4px;
  }
  .contact-email {
    position: absolute; right: 8px; top: 284px;
    color: var(--white); font-size: 12.5px; display: flex; align-items: center; gap: 5px;
  }
  .contact-email svg { width: 10px; height: 8px; }

  .abn { position: absolute; left: 62px; top: 128px; font-size: 18px; color: var(--ink); }

  .services-title {
    position: absolute; right: 20px; top: 158px;
    font-size: 21px; font-weight: 600; color: var(--brand-blue);
  }
  .service-list { position: absolute; left: 30px; right: 18px; top: 196px; list-style: none; }
  .service-list__item {
    display: flex; gap: 8px; font-size: 13.5px; color: var(--ink);
    line-height: 19px; margin-bottom: 9px;
  }
  .service-list__label {
    color: var(--brand-blue); font-weight: 600; font-size: 15.5px;
    flex: 0 0 72px; text-align: right;
  }
  .service-list__text { flex: 1; text-align: right; }
  .services-general {
    position: absolute; right: 20px; top: 275px;
    color: var(--brand-blue); font-size: 16px; font-weight: 600; letter-spacing: 1.6px;
  }
</style>
</head>
<body>
<main class="sheet">
  <p class="side-label side-label--one">Front-1</p>
  <p class="side-label side-label--two">Front-2</p>

  <!-- Front, grey version -->
  <section class="card card--front-grey">
    <svg class="card__wave" viewBox="0 0 540 308" preserveAspectRatio="none" aria-hidden="true">
      <path d="M0,252 C150,322 300,300 540,165 L540,308 L0,308 Z" fill="var(--brand-blue)"/>
      <path d="M0,258 C130,300 300,300 540,168" fill="none" stroke="var(--brand-blue-light)" stroke-width="12"/>
      <path d="M0,264 C110,285 150,290 200,290" fill="none" stroke="var(--card-grey)" stroke-width="5"/>
      <path d="M45,258 C210,300 380,232 540,166" fill="none" stroke="#1d1d1f" stroke-width="5"/>
    </svg>
    <h1 class="brand-name"><span class="brand-name__main">Brightway Haul</span><span class="brand-name__sub">&amp; Upkeep Services</span></h1>
    <p class="contact-phone">
      <svg viewBox="0 0 16 16" aria-hidden="true"><circle cx="8" cy="8" r="7.3" fill="none" stroke="var(--brand-blue)" stroke-width="1.2"/><path d="M5.2,4 L6.6,4 L7.2,6 L6.3,6.8 C6.8,8 7.8,9 9,9.5 L9.8,8.6 L11.8,9.2 L11.8,10.6 C8,11.2 4.6,7.8 5.2,4 Z" fill="var(--brand-blue)"/></svg>
      0487650392
    </p>
    <p class="contact-web">www.brightwayhaul.com.au</p>
    <p class="contact-email">
      <svg viewBox="0 0 10 8" aria-hidden="true"><rect x="0.5" y="0.5" width="9" height="7" fill="none" stroke="#fff"/><path d="M0.5,0.8 L5,4.5 L9.5,0.8" fill="none" stroke="#fff"/></svg>
      brightwayhaulandupkeep@mailbox.example
    </p>
  </section>

  <!-- Front, black version -->
  <section class="card card--front-black">
    <svg class="card__wave" viewBox="0 0 540 308" preserveAspectRatio="none" aria-hidden="true">
      <path d="M0,258 C150,322 300,298 540,170 L540,308 L0,308 Z" fill="var(--brand-blue)"/>
      <path d="M0,262 C140,305 300,300 540,172" fill="none" stroke="var(--brand-blue-light)" stroke-width="12"/>
      <path d="M0,280 C120,308 320,300 540,180" fill="none" stroke="var(--card-black)" stroke-width="6"/>
    </svg>
    <h1 class="brand-name"><span class="brand-name__main">Brightway Haul</span><span class="brand-name__sub">&amp; Upkeep Services</span></h1>
    <p class="contact-phone">
      <svg viewBox="0 0 16 16" aria-hidden="true"><circle cx="8" cy="8" r="7.3" fill="none" stroke="#fff" stroke-width="1.2"/><path d="M5.2,4 L6.6,4 L7.2,6 L6.3,6.8 C6.8,8 7.8,9 9,9.5 L9.8,8.6 L11.8,9.2 L11.8,10.6 C8,11.2 4.6,7.8 5.2,4 Z" fill="#fff"/></svg>
      0487650392
    </p>
    <p class="contact-web">www.brightwayhaul.com.au</p>
    <p class="contact-email">
      <svg viewBox="0 0 10 8" aria-hidden="true"><rect x="0.5" y="0.5" width="9" height="7" fill="none" stroke="#fff"/><path d="M0.5,0.8 L5,4.5 L9.5,0.8" fill="none" stroke="#fff"/></svg>
      brightwayhaulandupkeep@mailbox.example
    </p>
  </section>

  <!-- Back -->
  <section class="card card--back">
    <h2 class="brand-name"><span class="brand-name__main">Brightway Haul</span><span class="brand-name__sub">&amp; Upkeep Services</span></h2>
    <p class="abn">ABN 58190442736</p>
    <h3 class="services-title">Services we offer</h3>
    <ul class="service-list">
      <li class="service-list__item">
        <span class="service-list__label">CLEAN:</span>
        <span class="service-list__text" style="text-align:left">Windows, Gutters, Solar Panels, Driveways/paths, Carpets.</span>
      </li>
      <li class="service-list__item">
        <span class="service-list__label">MOVE:</span>
        <span class="service-list__text">Small/medium Size House/office Moves, Large Item Pick-up<br>&amp; Delivery, Yard Clean-up And Removal.</span>
      </li>
    </ul>
    <p class="services-general">General maintenance and repairs.</p>
  </section>
</main>
</body>
</html>
```